TrailPeakMotion-fitness app follows the owner or client moves, let them monitor their weight & fitness

TrailPeakMotion -fitness app, the avatar changes & evolve with the data logged in. the avatar resembles the client. the avatar weight looks like the client. When the client loses weight or gains weight, the avatar changes.
A brief is attached, check it out and get back to me with you're design.

Every week I will increase by 100€ instead.

Trailpeakmotion -fitness App Idea.
Two Business Logo.

March 2013 Ireland, the land of magic. Trailpeakmotion was born. Copy the client moves. With the avatar.
The app is about fitness, I have a vision and that you can be part of it.
Let's change the world together!
- the 1st page is about trailpeakmotion mission/founder/value of the company.
I will attach all information on Page(A)
after the intro, Terms and conditions poly/data policy ( the client has to agree and Sign before continuing. Then comes the page ParQ
the ParQ is a questionnaire asking the client to know more about them!
ParQ features the beginning: Create your personalized Avatar ( change clothes – if they choose no cloths, by default the avatar will have a pair of short- pant/hair/ eyes colour/ and select Body type: Ectomorph/ endomorph/ mesomorph or the client can select a mix body type.
Age select/ currant weight/ desired weight/ skin colour/ gender: male, female, Transgender, other.
Fitness goals: what the client desire how they are going to achieve it/ the measure they will take to achieve it or I don’t know option. The press continues / the app analyses all the data and create their personalise unique Avatar. That will look like the description they provided.
Page 2nd feature: they will see their full-body avatar.
Next, the client needs to continue completing more information.
Stress level select/ nutrition habits select/ and nutrition habit desired select/ injuries select/ allergies select/ history of any health complication question to answer/ Gp ( their Doctor name and number, to fill in/ and a person to contact in case of an emergency. Fill-in answer).
Page 3rd The Main Page. This results will depend on the answer of E-Wallet (5)
TrailPeakMotion-fitness Pro APP, Will analyse all the data and the app will suggest the best fitness program, nutrition plan, meditation advice to help them with stress/ and sleep hours they need to recover from after exercise/ base on their body type, fitness goal, and current stress level.
Main page Features: Keep in mind; the avatar changes form constantly, all depend on the information the client put on the profile setting.
1- the Avatar
- the can look Happy
- or sad – the reason why! Can tell the client all the reason for being that way and the solutions to make it better.
- Angry- Reason why! Can tell the client all the reason for being that way and the solutions to make it better.
- if the client gain weight, it will show on the avatar body.
- When the client loses weight the avatar will tell the client with a notification and it shows o the avatar body.
2- fitness check the app call Trenola and Stridewell fitness app, I like their page layout, it might show you what type of page I’m looking for and the quality that hoping or expecting.
- Muscle 3d full body when selecting a muscle it will show you the best exercises to work that particular muscle and weight recommendation. Check the app called
- Fitness Equipment to target each muscle and best suggestion for each muscle.
- Exercises all exercise available to get someone I top shape and the option to add more custom exercises. Liked exercise option/ search for exercises option/ reminder option.
- Nutrition Plans ( Vegan option/ paleo diet Option/ Keto diet/ build their own pers meal plan.
- Wellness Suggestions, tips raising your energy level
3- social Media
- Pictoria
- ChatLoop
- Boardly
- Circlenest
Feedback option
4- Music
- connect to Tunevault.
- Connect to playlist Custom
- Connect to Melodro
5- E-wallet
- buy a 1to1 personal training session ( only for members living in the country as
the founder)
- Buy 1 sessions/ 45Minutes 45€
- Buy 1sessions / 30 Minutes 35€
- Buy 1 session / 60 Minutes 55€
App subscription ( 2 options)
- Buy one Month subscription 7.99€ app
- Buy one Year Subscription for 107.88€ Share it with 10 people for the best deal 49.99€ for 12 months.
6- share it
on any social platform on the list
7- Picture Gallery
- before Pic
- after pic
8 – Deals & Offers
link to affiliated with other organization( trailpeakmotion will put all fitness deals and offers on this page.
9 –Contacts
- Gps number and information
-- Friend or family to contact during an emergency
10- Testimonials
- Reviews
11- To-do List
- Calendar bookings
- fitness goal planner
12- Chat On The app community
- a page where all the app members can chat if they open the portal and agree to it.
13- Profile settings
- account settings
14-Progress Tracker
15 – Connect Fit Device
-- Progression CHART.
- Junk food / sweet tracker (obviously the client need to log in what they eat each time.
Base on what they eat the Avatar will take shape/ increase weight or lose weight / change mood/ the client will know when they are doing something wrong or right base on how the avatar mood.
I this idea is yours to be part of something different, this idea is will donate for young and family who need help and support.

WELCOME TO TrailPeakMotion-fitness Private Studio
OUR MISSION
TrailPeakMotion an Ireland based company whose mission is to help you
complete your journey stronger, faster with confidence.
ABOUT TrailPeakMotion
TrailPeakMotion-fitness Was created from and inspire by the Irish strength and power to conquer any challenges, in 2013 after winning a boxing tournament in the national stadium. Driven by the desire to make a difference in the sports industry, I won that knight because my hunger for success was bigger than my opponents. TrailPeakMotion-fitness Private Studio, I decided to teach and coach people, how to improve their fitness components with all the experience I have under my belt. My Mission is to inspire and be inspired by the new young talents in need for an opportunity.
TrailPeakMotion-fitness Private Studio – Your energy is what keeps us moving and striving for a better and stronger united community. Fitness is the future & wellness is life.
I. OUR FOUNDER
Born and raised in the Caribbean, I started boxing when I was 19 years of age.
I started fighting to learn how to defend myself from bullying and protect my mother.
I started winning all my amateur fights, travelling around the world, the idea of travelling and the famous side of being a fighter kind started to like a little bit. My ambition didn’t stop there, it grew to aim for the stars and bigger plans.
I always dreamed of owning my own cloth brand and my own fitness gym. All over the Caribbean.
My peaceful Land (Dominican Rep, gave me the qualities to rise and achieve many goals. I believe- everything and anything is possible, once you have the right mindset and dedication to achieve it.
Trained by many of the best in coach in Ireland.
Now is time to share my knowledge.
OUR VALUES:
We value top quality Service and will ensure you have an amazing experience with TrailPeakMotion Fitness. If not, write to us and we’ll make it right.
II. GIVING BACK:
To help and support those in need in our communities.
10% of our earning will be used to help and support people in need in the Dominican Republic, Haiti and all the Caribbean. We support our young athletes with big dreams. Seeing them succeed is the best gift the world can give us all.
Good Luck to all who will take this challenge. Remember this is only the start, the winner will gain an extra bonus for completing this work. And the chance to continue working with us.
III. You Can check the app call fitness Duo or stridewell a fitness app
these fitness features and setting is the style and standard I am looking for.

Target Market(s)

Fitness/ Nutrition & well Being

Contact Information for Business Card

Trailpeakmotion@quillpost.example
0871234567
www.trailpeakmotionfitness.example
The logo is on my brief.
On the card, I want trailPeakMotion Fitness Pro.
I like an attractive colour like gold champagne on the main front side and on the back I want black and green to match the logo. sharp and professional style.

Font styles to use
Serif
Decorative
Script

Requirements
Must have
• Most have an option to create an avatar, to look like the client profile and weight/ hairstyle. This session is for the (App) https://vidshare.example/Qw82ZxPlmN
Ectomorph body type.
Endomorph body type.
mesomorph body type.
or a mix body type option.
base on the body type the client will be suggested by the trailpeakmotion the best plan for them.
Most have a challenges page: like squat challenge/ push-Ups challenge/ few fitness challenges to motivate the client.
Nice to have
• I would like to have every single muscle on the human body with all the exercises to work that particular muscle. like fitness duo or stride Well fitness app
Must have a progression chart, to show the client his/her fitness progression on their: strength/ speed/ push-ups/ flexibility/ Cardio or their V02 Max.
also, Fitness test option; every month or even every the client wishes the can test their fitness.

I found an Idea on the net: https://vidshare.example/Qw82ZxPlmN
Thank you, a step closer to a better world.

```html
<!DOCTYPE html>
<html lang="en">
<head>
<meta charset="utf-8">
<title>TrailPeakMotion Fitness – App Screens</title>
<link href="https://fonts.googleapis.com/css2?family=Rubik:wght@400;500;600&family=Roboto:wght@400;500&display=swap" rel="stylesheet">
<style>
:root{
  --stage:#e3ecf3;
  --green-top:#0cb90c;
  --green-mid:#2fd45a;
  --green-bottom:#44f2c4;
  --green-icon:#12b312;
  --green-text:#14a814;
  --white:#ffffff;
  --panel:#eef0f5;
  --ink:#222426;
  --ink-soft:#3d4247;
  --divider:#d6dae0;
  --dark-btn:#2b2b2b;
  --today:#e53030;
}
*{box-sizing:border-box;margin:0;padding:0}
html,body{width:1200px;height:846px;overflow:hidden}
body{background:var(--stage);font-family:"Roboto",sans-serif;position:relative;color:var(--ink)}
.screen{position:absolute;top:118px;width:274px;height:618px;border-radius:24px;overflow:hidden;
  background:linear-gradient(180deg,var(--green-top) 0%,var(--green-mid) 45%,var(--green-bottom) 100%)}
.screen--todo{left:103px}
.screen--reviews{left:463px}
.screen--social{left:823px}
.app-bar{position:absolute;top:36px;left:0;width:100%;height:24px;display:flex;align-items:center;justify-content:center;
  font-family:"Rubik",sans-serif;font-size:15px;color:var(--white)}
.app-bar .back{position:absolute;left:12px;top:3px;display:flex;align-items:center;gap:6px;font-size:13px;font-weight:500}
.app-bar .search{position:absolute;right:12px;top:3px}
/* To do list */
.plan-hero{position:absolute;left:12px;top:74px;width:246px;height:101px;
  background:linear-gradient(120deg,#4a5054,#8b8f92 55%,#3b3f42);display:flex;flex-direction:column;align-items:center;justify-content:center;color:var(--white)}
.plan-hero h2{font-family:"Rubik",sans-serif;font-weight:500;font-size:16px}
.plan-hero p{font-size:10px;margin-top:4px}
.calendar{position:absolute;left:12px;top:175px;width:246px;background:var(--white);border-bottom:4px solid var(--green-mid)}
.calendar .row{display:grid;grid-template-columns:1.1fr 1fr .9fr 1.1fr 1.1fr .8fr .8fr}
.calendar .days span{height:31px;display:flex;align-items:center;justify-content:center;font-size:8.5px;border-right:1px solid var(--divider);border-bottom:1px solid var(--divider)}
.calendar .dates span{height:35px;display:flex;align-items:center;justify-content:center;font-size:13px;border-right:1px solid var(--divider)}
.calendar span:last-child{border-right:none}
.calendar .today{width:18px;height:18px;border-radius:50%;background:var(--today);color:var(--white);display:flex;align-items:center;justify-content:center;font-size:11px}
.task{position:absolute;left:12px;width:246px;height:67px;background:#f6f8fa;display:flex;align-items:center;padding-left:10px}
.task .thumb{width:42px;height:42px;border-radius:50%;background:radial-gradient(circle at 40% 40%,#c9b8a8,#4e4440)}
.task .info{margin-left:13px;flex:1}
.task .title{font-size:12px}
.task .sub{font-size:9.5px;margin-top:4px}
.task .time{font-size:10px;color:var(--green-text);margin-top:6px;display:flex;align-items:center;gap:4px}
.task .go{margin-right:12px}
/* Testimonials */
.brand-name{position:absolute;top:82px;width:100%;text-align:center;font-family:"Rubik",sans-serif;font-size:14px;color:#e9fff0;letter-spacing:.5px}
.review{position:absolute;left:15px;width:244px;height:120px;border:1.5px solid rgba(255,255,255,.85);border-radius:3px;background:rgba(10,150,80,.35);color:var(--white)}
.review .avatar{position:absolute;left:13px;top:17px;width:52px;height:52px;border-radius:50%;border:2px solid var(--white);background:radial-gradient(circle at 45% 40%,#6b5148,#1e1714)}
.review .head{position:absolute;left:80px;top:14px;display:flex;align-items:center;gap:6px;font-family:"Rubik",sans-serif;font-weight:500;font-size:12px}
.review .head .q{font-size:22px;line-height:1;height:16px}
.review .head .stars{font-size:10px;letter-spacing:1px;margin-left:14px}
.review p{position:absolute;left:80px;top:41px;width:160px;font-size:10px;line-height:13.3px}
.more-btn{position:absolute;left:14px;top:542px;width:246px;height:39px;background:var(--dark-btn);border-radius:2px;color:var(--white);font-family:"Rubik",sans-serif;font-weight:500;font-size:13px;display:flex;align-items:center;justify-content:center;letter-spacing:.3px}
/* Social */
.tile{position:absolute;width:117px;height:106px;background:var(--white);border-radius:2px;display:flex;flex-direction:column;align-items:center;padding-top:16px;font-family:"Rubik",sans-serif;font-weight:500;font-size:12.5px;color:var(--ink)}
.tile .dot{width:51px;height:51px;border-radius:50%;background:var(--green-icon);margin-bottom:15px}
.feed{position:absolute;left:18px;top:192px;width:241px;height:284px;background:var(--panel)}
.feed::before{content:"";position:absolute;top:-7px;left:171px;border:7px solid transparent;border-top:0;border-bottom-color:var(--panel)}
.post{position:relative;border-bottom:1px solid var(--divider);padding:0 16px}
.post .pic{position:absolute;width:42px;height:42px;border-radius:50%;border:2px solid var(--white);background:radial-gradient(circle at 50% 40%,#d8c2b1,#4f5864)}
.post h4{font-family:"Rubik",sans-serif;font-weight:500;font-size:12.5px;color:var(--ink-soft)}
.post p{font-size:11px;line-height:15px;color:var(--ink-soft);margin-top:4px}
.post--a{height:88px;padding-top:22px}
.post--a .pic{right:10px;top:14px}
.post--b{height:75px;padding-left:66px;padding-top:20px}
.post--b .pic{left:10px;top:14px}
.post--b p{margin-top:2px;font-size:12px}
.post--c{height:77px;padding-top:20px}
.post--c .pic{right:10px;top:6px}
.view-more{display:block;text-align:center;margin-top:14px;font-size:11.5px;color:var(--green-text);text-decoration:underline}
</style>
</head>
<body>

<section class="screen screen--todo">
  <header class="app-bar">
    <span class="back"><svg width="15" height="14" viewBox="0 0 15 14"><path d="M7 1 1 7l6 6M1 7h13" stroke="#fff" stroke-width="2.6" fill="none" stroke-linecap="round" stroke-linejoin="round"/></svg></span>
    To do List
    <svg class="search" width="15" height="15" viewBox="0 0 15 15"><circle cx="6" cy="6" r="4.6" stroke="#fff" stroke-width="2" fill="none"/><path d="m9.5 9.5 4 4" stroke="#fff" stroke-width="2.4" stroke-linecap="round"/></svg>
  </header>
  <div class="plan-hero" role="img" aria-label="Photo of a woman training in the gym">
    <h2>Personal Plan</h2>
    <p>Today, June 4</p>
  </div>
  <div class="calendar">
    <div class="row days"><span>SUN</span><span>MON</span><span>TUE</span><span>WED</span><span>THUR</span><span>FRI</span><span>SAT</span></div>
    <div class="row dates"><span>1</span><span><b class="today">2</b></span><span>3</span><span>4</span><span>5</span><span>6</span><span>7</span></div>
  </div>
  <div class="task" style="top:246px"><div class="thumb" role="img" aria-label="Workout photo"></div><div class="info"><div class="title">Nemo enim ipsam</div><div class="sub">quia voluptas sit</div><div class="time"><svg width="8" height="8" viewBox="0 0 8 8"><circle cx="4" cy="4" r="3.2" stroke="#14a814" stroke-width="1.3" fill="none"/><path d="M4 2v2l1.3 1" stroke="#14a814" stroke-width="1" fill="none"/></svg>10 min</div></div><svg class="go" width="15" height="15" viewBox="0 0 15 15"><circle cx="7.5" cy="7.5" r="6.8" stroke="#666" fill="none"/><path d="m6.3 4.6 3 2.9-3 2.9" stroke="#666" fill="none"/></svg></div>
  <div class="task" style="top:319px"><div class="thumb" role="img" aria-label="Workout photo"></div><div class="info"><div class="title">Nemo enim ipsam</div><div class="sub">quia voluptas sit</div><div class="time"><svg width="8" height="8" viewBox="0 0 8 8"><circle cx="4" cy="4" r="3.2" stroke="#14a814" stroke-width="1.3" fill="none"/><path d="M4 2v2l1.3 1" stroke="#14a814" stroke-width="1" fill="none"/></svg>10 min</div></div><svg class="go" width="15" height="15" viewBox="0 0 15 15"><circle cx="7.5" cy="7.5" r="6.8" stroke="#666" fill="none"/><path d="m6.3 4.6 3 2.9-3 2.9" stroke="#666" fill="none"/></svg></div>
  <div class="task" style="top:392px"><div class="thumb" role="img" aria-label="Workout photo"></div><div class="info"><div class="title">Nemo enim ipsam</div><div class="sub">quia voluptas sit</div><div class="time"><svg width="8" height="8" viewBox="0 0 8 8"><circle cx="4" cy="4" r="3.2" stroke="#14a814" stroke-width="1.3" fill="none"/><path d="M4 2v2l1.3 1" stroke="#14a814" stroke-width="1" fill="none"/></svg>10 min</div></div><svg class="go" width="15" height="15" viewBox="0 0 15 15"><circle cx="7.5" cy="7.5" r="6.8" stroke="#666" fill="none"/><path d="m6.3 4.6 3 2.9-3 2.9" stroke="#666" fill="none"/></svg></div>
  <div class="task" style="top:464px"><div class="thumb" role="img" aria-label="Workout photo"></div><div class="info"><div class="title">Nemo enim ipsam</div><div class="sub">quia voluptas sit</div><div class="time"><svg width="8" height="8" viewBox="0 0 8 8"><circle cx="4" cy="4" r="3.2" stroke="#14a814" stroke-width="1.3" fill="none"/><path d="M4 2v2l1.3 1" stroke="#14a814" stroke-width="1" fill="none"/></svg>10 min</div></div><svg class="go" width="15" height="15" viewBox="0 0 15 15"><circle cx="7.5" cy="7.5" r="6.8" stroke="#666" fill="none"/><path d="m6.3 4.6 3 2.9-3 2.9" stroke="#666" fill="none"/></svg></div>
  <div class="task" style="top:537px"><div class="thumb" role="img" aria-label="Workout photo"></div><div class="info"><div class="title">Nemo enim ipsam</div><div class="sub">quia voluptas sit</div><div class="time"><svg width="8" height="8" viewBox="0 0 8 8"><circle cx="4" cy="4" r="3.2" stroke="#14a814" stroke-width="1.3" fill="none"/><path d="M4 2v2l1.3 1" stroke="#14a814" stroke-width="1" fill="none"/></svg>10 min</div></div><svg class="go" width="15" height="15" viewBox="0 0 15 15"><circle cx="7.5" cy="7.5" r="6.8" stroke="#666" fill="none"/><path d="m6.3 4.6 3 2.9-3 2.9" stroke="#666" fill="none"/></svg></div>
</section>

<section class="screen screen--reviews" role="img" aria-label="Green-toned photo of an athlete behind the reviews">
  <header class="app-bar">
    <span class="back"><svg width="15" height="14" viewBox="0 0 15 14"><path d="M7 1 1 7l6 6M1 7h13" stroke="#fff" stroke-width="2.6" fill="none" stroke-linecap="round" stroke-linejoin="round"/></svg></span>
    Testimonials
    <svg class="search" width="15" height="15" viewBox="0 0 15 15"><circle cx="6" cy="6" r="4.6" stroke="#fff" stroke-width="2" fill="none"/><path d="m9.5 9.5 4 4" stroke="#fff" stroke-width="2.4" stroke-linecap="round"/></svg>
  </header>
  <div class="brand-name">TrailPeakMotion</div>
  <article class="review" style="top:139px"><div class="avatar" role="img" aria-label="Reviewer portrait"></div><div class="head"><span class="q">“</span>John Doe<span class="stars">★★★★★</span></div><p>Sed ut perspiciatis unde omnis iste natus error sit voluptatem accusantium doloremque lauium, totam rem aperiam, eaque ipsa quae ab illo inventore</p></article>
  <article class="review" style="top:272px"><div class="avatar" role="img" aria-label="Reviewer portrait"></div><div class="head"><span class="q">“</span>John Doe<span class="stars">★★★★★</span></div><p>Sed ut perspiciatis unde omnis iste natus error sit voluptatem accusantium doloremque lauium, totam rem aperiam, eaque ipsa quae ab illo inventore</p></article>
  <article class="review" style="top:404px"><div class="avatar" role="img" aria-label="Reviewer portrait"></div><div class="head"><span class="q">“</span>John Doe<span class="stars">★★★★★</span></div><p>Sed ut perspiciatis unde omnis iste natus error sit voluptatem accusantium doloremque lauium, totam rem aperiam, eaque ipsa quae ab illo inventore</p></article>
  <div class="more-btn">VIEW MORE REVIEWS</div>
</section>

<section class="screen screen--social">
  <header class="app-bar">
    <span class="back"><svg width="15" height="14" viewBox="0 0 15 14"><path d="M7 1 1 7l6 6M1 7h13" stroke="#fff" stroke-width="2.6" fill="none" stroke-linecap="round" stroke-linejoin="round"/></svg>Back</span>
    <span style="margin-left:16px">Social Media</span>
    <svg class="search" width="15" height="15" viewBox="0 0 15 15"><circle cx="6" cy="6" r="4.6" stroke="#fff" stroke-width="2" fill="none"/><path d="m9.5 9.5 4 4" stroke="#fff" stroke-width="2.4" stroke-linecap="round"/></svg>
  </header>
  <div class="tile" style="left:17px;top:74px"><span class="dot"></span>Pictoria</div>
  <div class="tile" style="left:142px;top:74px"><span class="dot"></span>ChatLoop</div>
  <div class="feed">
    <div class="post post--a"><div class="pic" role="img" aria-label="Member portrait"></div><h4>John Doe</h4><p>Lorem ipsum dolor sit amet,<br>consectetur adipiscing elit, sed</p></div>
    <div class="post post--b"><div class="pic" role="img" aria-label="Member portrait"></div><h4>Manuel</h4><p>Nemo enim ipsam voluptate</p></div>
    <div class="post post--c"><div class="pic" role="img" aria-label="Member portrait"></div><h4>John Doe</h4><p>Lorem ipsum dolor sit amet,<br>consectetur adipiscing elit, sed</p></div>
    <a class="view-more">View More</a>
  </div>
  <div class="tile" style="left:17px;top:487px"><span class="dot"></span>Boardly</div>
  <div class="tile" style="left:142px;top:487px"><span class="dot"></span>Circlenest</div>
</section>

</body>
</html>
```